Home Security Company Business Card

Looking for a eye catching business card that is non traditional and stands out but yet still looks professional. It should include all the pertinent information such as name, title, address, telephone, e-mail, website address should definitely stand out and then finally the logo.

Target Market(s)

Residential and Commercial accounts mostly upscale accounts

Industry/Entity Type

Security

Contact Information for Business Card

Name
Title
Address
Office #
Cell #
E-mail
Website

Font styles to use
Serif
Sans Serif

Requirements
Must have
• Logo, two sided color configuration
Nice to have
• You decide
Should not have
• There really aren't any.

```html
<!DOCTYPE html>
<html lang="en">
<head>
<meta charset="utf-8">
<title>Brightlock Protection Systems – Business Card</title>
<link href="https://fonts.googleapis.com/css2?family=Ubuntu:wght@400;500;700&display=swap" rel="stylesheet">
<style>
  :root {
    --page-bg: #e9e4dc;
    --card-gold: #ecbe50;
    --card-gold-light: #f2cd66;
    --card-maroon: #7b1416;
    --card-maroon-dark: #5e0e10;
    --ink-maroon: #7a1a14;
    --ink-grey: #8a7a55;
    --rule: #b89548;
    --ink-white: #ffffff;
    --accent-gold: #e0a93a;
  }
  * { box-sizing: border-box; margin: 0; padding: 0; }
  html, body {
    width: 1200px; height: 750px; overflow: hidden;
    background: var(--page-bg);
    font-family: "Ubuntu", "Helvetica Neue", Arial, sans-serif;
  }
  .canvas { position: relative; width: 1200px; height: 750px; }

  .card {
    position: absolute; top: 202px; height: 318px;
    border-radius: 18px; overflow: hidden;
    box-shadow: 0 6px 14px rgba(0,0,0,0.25);
  }
  .card--front { left: 28px; width: 560px; background: var(--card-gold); }
  .card--back { left: 614px; width: 558px; background: var(--card-maroon); }

  .edge-glow {
    position: absolute; top: 0; bottom: 0; width: 110px;
  }
  .card--front .edge-glow {
    right: 0;
    background: linear-gradient(90deg, rgba(242,205,102,0) 0%, var(--card-gold-light) 60%, rgba(196,140,40,0.55) 100%);
  }
  .card--back .edge-glow {
    left: 0;
    background: linear-gradient(90deg, var(--card-maroon-dark) 0%, rgba(123,20,22,0) 100%);
  }

  /* Front brand */
  .brand { position: absolute; display: flex; align-items: center; }
  .brand-dot { border-radius: 50%; flex: none; }
  .brand-name { font-weight: 500; line-height: 1.05; text-transform: uppercase; }
  .brand-name .brand-sub { display: block; }

  .card--front .brand { left: 42px; top: 40px; gap: 12px; }
  .card--front .brand-dot { width: 62px; height: 62px; background: var(--ink-maroon); }
  .card--front .brand-name { color: var(--ink-maroon); font-size: 17px; }
  .card--front .brand-sub { font-size: 8.5px; letter-spacing: 0.3px; margin-top: 2px; }

  .person { position: absolute; left: 42px; top: 158px; width: 420px; }
  .person-name { font-size: 24px; font-weight: 700; color: var(--ink-maroon); letter-spacing: 0.2px; }
  .person-title-row { display: flex; align-items: center; gap: 6px; margin-top: -2px; }
  .person-title { font-size: 15px; color: var(--ink-grey); }
  .person-title-rule { flex: 1; height: 1px; background: var(--rule); margin-top: 4px; }

  .contacts { position: absolute; left: 42px; top: 214px; list-style: none; }
  .contacts li {
    display: flex; align-items: center; gap: 8px;
    font-size: 16px; line-height: 19.5px; color: var(--ink-maroon);
  }
  .contacts svg { width: 13px; height: 13px; fill: var(--ink-maroon); flex: none; }

  /* Back */
  .card--back .brand { left: 192px; top: 66px; gap: 18px; }
  .card--back .brand-dot {
    width: 120px; height: 120px;
    background: radial-gradient(circle at 40% 40%, #f6dc8a 0%, var(--accent-gold) 70%, #b57c22 100%);
  }
  .card--back .brand-name { color: var(--ink-white); font-size: 27px; }
  .card--back .brand-sub { font-size: 13.5px; margin-top: 2px; }

  .website {
    position: absolute; left: 0; right: 0; top: 252px;
    text-align: center; padding-left: 130px;
    font-size: 16px; font-weight: 500; color: var(--ink-white); letter-spacing: 0.2px;
  }
</style>
</head>
<body>
<main class="canvas">

  <section class="card card--front" aria-label="Card front">
    <div class="edge-glow"></div>

    <div class="brand">
      <span class="brand-dot"></span>
      <span class="brand-name">Brightlock<span class="brand-sub">Protection Systems Inc.</span></span>
    </div>

    <div class="person">
      <h1 class="person-name">Daniel Mercer</h1>
      <div class="person-title-row">
        <span class="person-title">Owner</span>
        <span class="person-title-rule"></span>
      </div>
    </div>

    <ul class="contacts">
      <li>
        <svg viewBox="0 0 16 16" aria-hidden="true"><path d="M1 6c0-2 3-4 7-4s7 2 7 4v1h-4V5.5H5V7H1z"/><rect x="3" y="8" width="10" height="6" rx="1.5"/></svg>
        +310 5550-1234
      </li>
      <li>
        <svg viewBox="0 0 16 16" aria-hidden="true"><path d="M4 1l2.5 3.5L5 6.5c1 2 2.5 3.5 4.5 4.5l2-1.5L15 12l-2 3C7 15 1 9 1 3z"/></svg>
        +3105550-67890
      </li>
      <li>
        <svg viewBox="0 0 16 16" aria-hidden="true"><path d="M1 3h14v10H1zm1.5 1.5v.3L8 9l5.5-4.2v-.3zm0 2.1v4.9h11V6.6L8 10.8z"/></svg>
        info@danielmercermail.com
      </li>
      <li>
        <svg viewBox="0 0 16 16" aria-hidden="true"><path d="M8 0a5.5 5.5 0 0 0-5.5 5.5C2.5 10 8 16 8 16s5.5-6 5.5-10.5A5.5 5.5 0 0 0 8 0zm0 8a2.5 2.5 0 1 1 0-5 2.5 2.5 0 0 1 0 5z"/></svg>
        240 Harbor Lane Aurora, Illinois 60505
      </li>
    </ul>
  </section>

  <section class="card card--back" aria-label="Card back">
    <div class="edge-glow"></div>

    <div class="brand">
      <span class="brand-dot"></span>
      <span class="brand-name">Brightlock<span class="brand-sub">Protection Systems Inc.</span></span>
    </div>

    <p class="website">www.brightlockprotectionsystems.com</p>
  </section>

</main>
</body>
</html>
```